Estate Agent Board Design

Most eye-catching, elegant estate agent board
Company logo should stand out
Korvimark & TREG should be small but visible.

On the board must be:

"FOR SALE"
logos
website zhbproperties.co.uk
tel number 01632 960418

It Company

```html
<!DOCTYPE html>
<html lang="en">
<head>
<meta charset="UTF-8">
<title>zhb Sales &amp; Lettings – For Sale Board</title>
<link rel="stylesheet" href="https://fonts.googleapis.com/css2?family=Archivo+Black&family=Roboto:wght@500;700&display=swap">
<style>
  :root{
    --green-dark:#16472a;
    --green:#1f5c33;
    --white:#ffffff;
    --frame:#b9bcbf;
    --ink:#2b2b2b;
    --badge-blue:#1d5fa8;
    --badge-navy:#1b2a4a;
    --page:#eef0f1;
  }
  *{margin:0;padding:0;box-sizing:border-box;}
  html,body{width:1200px;height:798px;overflow:hidden;background:var(--page);}
  .canvas{position:relative;width:1200px;height:798px;}
  .board{
    position:absolute;left:132px;top:40px;width:935px;height:718px;
    background:var(--white);border:10px solid var(--frame);
  }
  .brand{position:absolute;left:168px;top:56px;display:flex;align-items:flex-start;}
  .brand-mark{width:218px;height:218px;background:var(--green-dark);}
  .brand-text{margin-left:18px;}
  .brand-name{
    font-family:"Archivo Black",sans-serif;font-size:190px;line-height:150px;
    color:var(--green);letter-spacing:-6px;
  }
  .brand-tagline{
    font-family:"Roboto",sans-serif;font-weight:500;font-size:33px;color:var(--ink);
    margin-top:22px;letter-spacing:0.5px;
  }
  .sale-band{
    position:absolute;left:0;top:328px;width:100%;height:140px;background:var(--green);
    display:flex;align-items:center;justify-content:center;
  }
  .sale-band h1{
    font-family:"Archivo Black",sans-serif;font-weight:400;font-size:112px;color:var(--white);
    letter-spacing:4px;line-height:1;
  }
  .contact-row{
    position:absolute;left:0;top:500px;width:100%;height:112px;
  }
  .badge{position:absolute;top:6px;width:100px;height:100px;}
  .badge-korvimark{left:40px;border-radius:14px;background:var(--badge-navy);}
  .badge-treg{right:40px;border-radius:50%;background:var(--badge-blue);border:6px solid #d8dde3;}
  .phone{position:absolute;left:180px;top:22px;display:flex;align-items:center;}
  .phone svg{width:52px;height:66px;}
  .phone-number{
    font-family:"Archivo Black",sans-serif;font-size:60px;color:var(--ink);
    margin-left:24px;letter-spacing:3px;line-height:1;
  }
  .web-strip{
    position:absolute;left:0;bottom:0;width:100%;height:64px;background:var(--green);
    display:flex;align-items:center;justify-content:center;
    font-family:"Roboto",sans-serif;font-weight:500;font-size:27px;color:var(--white);letter-spacing:5px;
  }
  .web-strip b{font-weight:700;}
</style>
</head>
<body>
<div class="canvas">
  <div class="board">
    <div class="brand">
      <div class="brand-mark" aria-hidden="true"></div>
      <div class="brand-text">
        <div class="brand-name">zhb</div>
        <div class="brand-tagline">SALES &amp; LETTINGS</div>
      </div>
    </div>

    <div class="sale-band"><h1>FOR SALE</h1></div>

    <div class="contact-row">
      <div class="badge badge-korvimark" role="img" aria-label="Korvimark member badge"></div>
      <div class="phone">
        <svg viewBox="0 0 40 52" aria-hidden="true">
          <path d="M10 2 L17 12 L12 17 Q14 30 24 38 L30 33 L38 42 L31 50 Q8 44 3 12 Z" fill="var(--green)"/>
        </svg>
        <span class="phone-number">01632 960418</span>
      </div>
      <div class="badge badge-treg" role="img" aria-label="TREG licensed badge"></div>
    </div>

    <div class="web-strip">www.<b>zhb</b>properties.co.uk</div>
  </div>
</div>
</body>
</html>
```